Vantrel System Web Page Design

This project is to design 6 pages of a web based medical system for clinics, hospitals, drugs suppliers, general items suppliers, insurance company, laboratories and patients (basically all parties which could be involved in).We want the designs of the browser, button, icon and layout are based on Zeltor, which is user friendly, looks professional, simple and neat but with powerful functions. We have uploaded few pictures of another system, please do not copy its design because this is not what we are looking for, the pictures are for you to know the elements should be included in our pages. Vantrel web-base system, design 6 pages1. Login PageShould include the following elements-company id with input field-login id with input field-password with input field2. Main Page (Navigation page)Should include the following elements-Appointment-Consultation-Patient-Drugs inventory -General supplies inventory -Laboratory-Suppliers-Insurance-Reports 3. Appointment PageShould include all the the elements in the respective pictures plus the followings-Daily View, Weekly View, Monthly View buttons4. Consultation PageShould include all the the elements in the respective picture5. Patient Page5.1 General information Should include all the the elements in the respective picture5.2 medical history/lab reportsShould include all the the elements in the respective picture plus the followings-Notify patient button-Share report button.
Updated on 28 Nov:
Please stop using Harbor Suite in your designs which is not the name of our system. We have just rename our system to Vantrel, please take note.
We need the system to look professional not playful, do not use too many colors and playful icons.

```html
<!DOCTYPE html>
<html lang="en">
<head>
<meta charset="UTF-8">
<title>Vantrel – Log In</title>
<link rel="stylesheet" href="https://fonts.googleapis.com/css2?family=Open+Sans:ital,wght@0,400;1,400&display=swap">
<style>
  :root {
    --page-bg: #fafafa;
    --brand-blue: #0a78f5;
    --field-border: #c9c9c9;
    --field-bg: #ffffff;
    --placeholder: #b5b5b5;
    --link-text: #1a1a1a;
    --button-text: #ffffff;
  }
  * { box-sizing: border-box; margin: 0; padding: 0; }
  html, body {
    width: 1200px;
    height: 675px;
    overflow: hidden;
    background: var(--page-bg);
    font-family: "Open Sans", Arial, sans-serif;
  }
  .login-screen {
    position: relative;
    width: 1200px;
    height: 675px;
  }
  .brand-name {
    position: absolute;
    top: 146px;
    left: 0;
    width: 1200px;
    text-align: center;
    font-size: 54px;
    font-weight: 400;
    color: var(--brand-blue);
    letter-spacing: 1px;
    line-height: 72px;
  }
  .login-form {
    position: absolute;
    top: 287px;
    left: 450px;
    width: 300px;
  }
  .form-field {
    display: block;
    width: 300px;
    height: 37px;
    margin-bottom: 16px;
    padding: 0 20px;
    border: 1.5px solid var(--field-border);
    border-radius: 5px;
    background: var(--field-bg);
    font-family: inherit;
    font-size: 13.5px;
    color: #333;
  }
  .form-field::placeholder { color: var(--placeholder); }
  .login-button {
    display: block;
    width: 300px;
    height: 37px;
    margin-top: 24px;
    border: none;
    border-radius: 5px;
    background: var(--brand-blue);
    color: var(--button-text);
    font-family: inherit;
    font-size: 13.5px;
  }
  .forgot-link {
    display: block;
    margin-top: 13px;
    text-align: center;
    font-size: 11.5px;
    font-style: italic;
    color: var(--link-text);
    text-decoration: underline;
  }
</style>
</head>
<body>
  <main class="login-screen">
    <div class="brand-name">Vantrel</div>
    <form class="login-form">
      <input class="form-field" type="text" placeholder="Company ID">
      <input class="form-field" type="text" placeholder="Login ID">
      <input class="form-field" type="password" placeholder="Password">
      <button class="login-button" type="button">Log In</button>
      <a class="forgot-link" href="#">Forget Password ?</a>
    </form>
  </main>
</body>
</html>
```